Harborview Optical -Window Poster (Optometrist)

We are an optometry practice and we need a poster for a new store promotion for our window highlighting we now also sell 2 pairs of glasses as a package deal. The size will be 1300mm width x 1900mm height

The artwork will be displayed as a fabric banner in our shop window. We have 7 other banners with different services our business provides. The words needs to standout for passers by and the cars stopped at the traffic lights out front of our business. We already have signs with our logos phone number etc. so we won't need them included in the poster.

It would need to include the following information.

Two pair packages now available*

*Conditions apply

The artwork will be displayed as a fabric banner in our shop window. We have 7 other banners with different services our business provides. The words needs to standout for passers by and the cars stopped at the traffic lights out front of our business. We already have signs with our logos phone number etc. so we won't need them included in the poster. Thank you for your work it's amazing Added Saturday, February 18, 2017

The artwork will be displayed as a fabric banner in our shop window. We have 7 other banners with different services our business provides. The words needs to standout for passers by and the cars stopped at the traffic lights out front of our business. We already have signs with our logos phone number etc. so we won't need them included in the poster. Added Saturday, February 18, 2017

Target Market(s)

Cars driving past and stopped at traffic lights outside our store.

Industry/Entity Type

Optician

Requirements
Must have
• Poster must say:
• Two pair packages now available*
• *Conditions apply

```html
<!DOCTYPE html>
<html lang="en">
<head>
<meta charset="utf-8">
<title>Harborview Optical – Two Pair Packages Window Poster</title>
<link rel="stylesheet" href="https://fonts.googleapis.com/css2?family=Bebas+Neue&display=swap">
<style>
  :root {
    --poster-black: #000000;
    --headline-white: #ffffff;
    --offer-orange: #f5a418;
    --terms-yellow: #f7e23b;
    --rule-white: #f2f2f2;
    --flare-grey: rgba(150, 160, 175, 0.55);
    --burst-tone: rgba(70, 40, 20, 0.35);
  }
  html, body {
    margin: 0;
    padding: 0;
    width: 962px;
    height: 1200px;
    overflow: hidden;
    background: var(--poster-black);
  }
  .poster {
    position: relative;
    width: 962px;
    height: 1200px;
    background: var(--poster-black);
    font-family: "Bebas Neue", "Arial Narrow", sans-serif;
    overflow: hidden;
  }
  .light-streaks {
    position: absolute;
    left: 0;
    top: 40px;
    width: 962px;
    height: 160px;
    background:
      radial-gradient(ellipse 45px 22px at 40px 175px, var(--flare-grey), transparent 70%),
      linear-gradient(90deg, transparent 0%, rgba(90, 105, 125, 0.35) 25%, transparent 55%) 0 40px / 100% 6px no-repeat,
      linear-gradient(90deg, transparent 45%, rgba(110, 120, 140, 0.35) 75%, rgba(60, 75, 100, 0.4) 100%) 0 90px / 100% 6px no-repeat;
  }
  .flare-right {
    position: absolute;
    left: 820px;
    top: 340px;
    width: 120px;
    height: 50px;
    background: radial-gradient(ellipse 35px 18px at center, var(--flare-grey), transparent 70%);
  }
  .burst {
    position: absolute;
    width: 330px;
    height: 300px;
    border-radius: 50%;
    background: radial-gradient(circle, var(--burst-tone) 0%, rgba(40, 25, 15, 0.15) 45%, transparent 70%);
  }
  .burst--left { left: 105px; top: 460px; }
  .burst--right { left: 660px; top: 420px; }
  .headline {
    position: absolute;
    left: 0;
    width: 962px;
    margin: 0;
    text-align: center;
    font-weight: 400;
    line-height: 1;
  }
  .headline--main {
    top: 218px;
    left: 10px;
    font-size: 133px;
    letter-spacing: 5px;
    color: var(--headline-white);
  }
  .headline--offer {
    top: 356px;
    left: 42px;
    font-size: 87px;
    letter-spacing: 3px;
    color: var(--offer-orange);
  }
  .rule {
    position: absolute;
    top: 452px;
    height: 3px;
    background: var(--rule-white);
  }
  .rule--left { left: 0; width: 355px; }
  .rule--right { left: 649px; width: 313px; }
  .terms {
    position: absolute;
    top: 1035px;
    left: 236px;
    width: 520px;
    margin: 0;
    font-size: 62px;
    letter-spacing: 6px;
    line-height: 1;
    color: var(--terms-yellow);
    white-space: nowrap;
  }
  .terms-rule {
    position: absolute;
    top: 1104px;
    left: 349px;
    width: 312px;
    height: 3px;
    background: linear-gradient(90deg, transparent, var(--rule-white) 20%, var(--rule-white) 80%, transparent);
  }
</style>
</head>
<body>
  <main class="poster">
    <div class="light-streaks" role="img" aria-label="Soft blue light streaks and lens flare"></div>
    <div class="flare-right" role="img" aria-label="Small lens flare glow"></div>
    <div class="burst burst--left" role="img" aria-label="Faint firework burst"></div>
    <div class="burst burst--right" role="img" aria-label="Faint firework burst"></div>

    <h1 class="headline headline--main">Two Pair Packages</h1>
    <p class="headline headline--offer">Now Available*</p>
    <div class="rule rule--left"></div>
    <div class="rule rule--right"></div>

    <p class="terms">*Conditions Apply</p>
    <div class="terms-rule"></div>
  </main>
</body>
</html>
```